Webshop Template

For our Webstore in UK we need a complete Template,
shoppingcart is Magento, the Shop is focussed on Download software,

the name: Kelvoramarket.co.uk

Check out some other good stores, like zandrilo.de
Updates

for example the Page from 

www.brunt.co.uk or

www.zandrilo.de

www.mokvelta.de

www.quarnepreis.de

The Logodesign which are in Consideration

http://www.plimvector.com/design/5520913/logo-design-by-tomek7ga

http://www.plimvector.com/design/5518207/logo-design-by-ivanoralba

http://www.plimvector.com/design/5517346/logo-design-by-granite-fables

http://www.plimvector.com/design/5516085/logo-design-by-quillotaste

http://www.plimvector.com/design/5515472/logo-design-by-tuvaro

http://www.plimvector.com/design/5514619/logo-design-by-lone-pine-graphic-

Target Market(s)

B2C - Consumer Marcet

Industry/Entity Type

Shop

```html
<!DOCTYPE html>
<html lang="en">
<head>
<meta charset="utf-8">
<title>Kelvoramarket.co.uk — Webshop Template</title>
<link rel="stylesheet" href="https://fonts.googleapis.com/css2?family=Arimo:wght@400;700&family=Cuprum:wght@400;700&display=swap">
<style>
  :root{
    --band:#4b4849;
    --band-dark:#3f3c3d;
    --page:#efefef;
    --sheet:#ffffff;
    --ink:#222222;
    --muted:#6b6b6b;
    --soft:#a8a8a8;
    --rule:#e2e2e2;
    --teal:#63b5c6;
    --footer:#4a4748;
    --footer-ink:#ffffff;
  }
  *{box-sizing:border-box;margin:0;padding:0}
  html,body{width:1127px;height:1200px;overflow:hidden}
  body{
    position:relative;
    font-family:"Arimo",Arial,sans-serif;
    color:var(--ink);
    background:linear-gradient(var(--band) 0,var(--band) 263px,var(--page) 263px);
  }
  a{color:inherit;text-decoration:none}

  /* top utility bar */
  .topbar{position:absolute;top:0;left:213px;width:704px;height:30px;display:flex;align-items:center;font-size:9px;color:#fff}
  .topbar .cart b{font-weight:700}
  .topbar .util{margin-left:auto;display:flex;align-items:center;gap:10px}
  .topbar .social{display:flex;gap:3px;margin-left:4px}
  .topbar .social span{width:9px;height:9px;border-radius:1px;background:#5b86c9}
  .topbar .social span:nth-child(2){background:#48a9d8}
  .topbar .social span:nth-child(3){background:#e58a2a}
  .topbar .sep{width:1px;height:10px;background:#777}

  /* white sheet */
  .sheet{position:absolute;top:30px;left:213px;width:704px;height:1113px;background:var(--sheet);border-radius:3px 3px 0 0}

  .logo{position:absolute;left:17px;top:31px;display:flex;align-items:center;gap:9px;font-family:"Arimo",Arial,sans-serif;font-weight:700;font-size:21px;letter-spacing:.5px}
  .logo i{width:19px;height:19px;border-radius:50%;background:#333;display:block}

  .search{position:absolute;left:536px;top:16px;width:149px;height:22px;border:1px solid #d4d4d4;border-radius:2px;background:linear-gradient(#f4f4f4,#fff)}
  .search svg{position:absolute;right:6px;top:4px}

  .nav{position:absolute;top:52px;left:350px;display:flex;gap:0;font-family:"Cuprum",sans-serif;font-size:11px;color:var(--soft)}
  .nav a{position:absolute;white-space:nowrap}
  .nav .current{color:var(--ink)}
  .head-rule{position:absolute;left:17px;right:17px;top:79px;height:1px;background:var(--rule)}

  .hero{position:absolute;left:17px;top:98px;width:669px;height:250px;overflow:hidden;
    background:linear-gradient(100deg,#1a1816 0%,#3a3230 35%,#6b5a52 55%,#2a2624 75%,#6c8a6e 100%)}
  .hero .price{position:absolute;left:14px;top:140px;font-family:"Cuprum",sans-serif;font-size:40px;color:#fff;line-height:1}
  .hero .price sup{font-size:18px;vertical-align:top;margin-right:4px}
  .hero .kicker{position:absolute;left:12px;top:194px;font-family:"Cuprum",sans-serif;font-size:19px;color:#23239a}
  .hero .tagline{position:absolute;left:12px;top:214px;font-family:"Cuprum",sans-serif;font-size:24px;color:#fff}

  /* section header pill */
  .pane-title{height:23px;border:1px solid #e6e6e6;border-radius:2px;background:linear-gradient(#fff,#f1f1f1);
    box-shadow:0 1px 2px rgba(0,0,0,.08);font-family:"Cuprum",sans-serif;font-size:15px;line-height:21px;padding-left:13px;color:#333}

  .sidebar{position:absolute;left:17px;top:368px;width:156px}
  .sidebar ul{list-style:none;padding:7px 0 0 14px;font-size:9.5px;color:var(--muted)}
  .sidebar li{height:20.3px;line-height:14px}
  .sidebar .info li{height:19px}
  .sidebar .block{margin-top:12px}
  .select{margin:14px 0 0 14px;width:125px;height:14px;border:1px solid #bdbdbd;font-size:8.5px;color:#999;line-height:12px;padding-left:4px;position:relative}
  .select b{position:absolute;right:1px;top:1px;width:10px;height:10px;border:1px solid #888;background:#eee}
  .select b::after{content:"";position:absolute;left:2px;top:3px;border:3px solid transparent;border-top:3px solid #333}
  .promo{margin-top:38px;height:141px;border:1px solid #ddd;position:relative;background:#fff}
  .promo .art{position:absolute;left:8px;top:14px;width:90px;height:118px;border-radius:8px;background:linear-gradient(160deg,#f2f2f2,#d8cbb4)}
  .promo p{position:absolute;right:2px;top:3px;font-family:"Cuprum",sans-serif;font-size:17px;line-height:17px;text-align:right;color:#222}
  .promo p sup{font-size:10px}

  .main{position:absolute;left:188px;top:368px;width:498px}
  .grid{display:grid;grid-template-columns:repeat(4,114px);column-gap:14px;row-gap:26px;margin-top:14px;margin-left:-3px}
  .product .thumb{height:133px;border:1px solid #dcdcdc;display:flex;align-items:center;justify-content:center;background:#fff}
  .product .shot{width:56px;height:72px;border-radius:2px}
  .product .name{margin-top:12px;font-size:10.5px;color:#555}
  .product .amount{margin-top:8px;font-size:9.5px;font-weight:700;color:#222}
  .product .actions{margin-top:10px;display:flex;gap:2px;padding-left:2px}
  .product .actions a{height:18px;border:1px solid #ddd;font-size:9.5px;line-height:16px;padding:0 5px;color:#888;background:#fff}
  .product .actions a.details{color:var(--teal)}

  .footer{position:absolute;left:213px;top:1143px;width:704px;height:57px;background:var(--footer);color:var(--footer-ink);font-size:8px;text-align:center}
  .footer .links{margin-top:16px;display:flex;justify-content:center;gap:0}
  .footer .links a{padding:0 10px;border-left:1px solid #888;line-height:9px}
  .footer .links a:first-child{border-left:0}
  .footer .copy{margin-top:6px}
  .footer .copy a{text-decoration:underline}
</style>
</head>
<body>
  <header class="topbar">
    <div class="cart"><b>Shopping cart</b>: &nbsp;Now in your cart &nbsp;<b>0</b> items</div>
    <div class="util">
      <span>Follow Us:<span class="social" style="display:inline-flex;vertical-align:middle"><span></span><span></span><span></span></span></span>
      <span class="sep"></span>
      <a href="#">Create an Account</a>
      <span class="sep"></span>
      <a href="#">Log In</a>
    </div>
  </header>

  <div class="sheet">
    <div class="logo"><i></i>LOGO</div>
    <div class="search">
      <svg width="13" height="13" viewBox="0 0 13 13"><circle cx="5" cy="5" r="3.8" fill="none" stroke="#444" stroke-width="1.6"/><line x1="7.8" y1="7.8" x2="12" y2="12" stroke="#444" stroke-width="2"/></svg>
    </div>
    <nav class="nav">
      <a class="current" style="left:0">Homepage</a>
      <a style="left:75px">What's New?</a>
      <a style="left:159px">Specials</a>
      <a style="left:223px">Reviews</a>
      <a style="left:287px">Contact Us</a>
    </nav>
    <div class="head-rule"></div>

    <section class="hero" role="img" aria-label="Banner photograph of a model in dark sunglasses with a green garment">
      <div class="price"><sup>$</sup>199.99</div>
      <div class="kicker">Rehen aligendi</div>
      <div class="tagline">Mpote et et ea sunt dolor</div>
    </section>

    <aside class="sidebar">
      <div class="pane-title">Categories</div>
      <ul>
        <li>Video Softwares</li><li>Security Softwares</li><li>Browsers</li><li>Antivirus</li>
        <li>Free Softwares</li><li>Operating Systems</li><li>ScreenSavers</li><li>Games</li><li>Utility Softwares</li>
      </ul>
      <div class="block pane-title">Manufacturers</div>
      <div class="select">please select<b></b></div>
      <div class="block pane-title" style="margin-top:20px">Information</div>
      <ul class="info">
        <li>Shipping &amp; Returns</li><li>Privacy Notice</li><li>Conditions of Use</li><li>Contact Us</li>
      </ul>
      <div class="promo">
        <div class="art" role="img" aria-label="Illustration of a figure pushing a hand truck with parcels"></div>
        <p>Free Shipping<br>over <sup>$</sup>99</p>
      </div>
    </aside>

    <main class="main">
      <div class="pane-title">Latest Products</div>
      <div class="grid">
        <div class="product"><div class="thumb"><div class="shot" role="img" aria-label="Green software box" style="background:linear-gradient(135deg,#2f6b2a,#9ccf4a)"></div></div><div class="name">Software Name</div><div class="amount">$96</div><div class="actions"><a>Add to Cart</a><a class="details">Details</a></div></div>
        <div class="product"><div class="thumb"><div class="shot" role="img" aria-label="Green software box with disc" style="width:70px;background:linear-gradient(135deg,#3a9a2a,#b6e07a 60%,#e8e8e8)"></div></div><div class="name">Software Name</div><div class="amount">$284</div><div class="actions"><a>Add to Cart</a><a class="details">Details</a></div></div>
        <div class="product"><div class="thumb"><div class="shot" role="img" aria-label="Orange office software box" style="background:linear-gradient(135deg,#f3c23a,#e46a1c)"></div></div><div class="name">Software Name</div><div class="amount">$383.76</div><div class="actions"><a>Add to Cart</a><a class="details">Details</a></div></div>
        <div class="product"><div class="thumb"><div class="shot" role="img" aria-label="Dark operating system box" style="background:linear-gradient(135deg,#1d2a5a,#7a2f8a)"></div></div><div class="name">Software Name</div><div class="amount">$151.29</div><div class="actions"><a>Add to Cart</a><a class="details">Details</a></div></div>

        <div class="product"><div class="thumb"><div class="shot" role="img" aria-label="Teal software box with red starburst" style="background:linear-gradient(135deg,#3aa7a0,#e8f2f0 70%,#d81c1c)"></div></div><div class="name">Software Name</div><div class="amount">$96</div><div class="actions"><a>Add to Cart</a><a class="details">Details</a></div></div>
        <div class="product"><div class="thumb"><div class="shot" role="img" aria-label="White tablet device" style="width:64px;height:26px;background:linear-gradient(#f4f4f4,#c9c9c9)"></div></div><div class="name">Software Name</div><div class="amount">$284</div><div class="actions"><a>Add to Cart</a><a class="details">Details</a></div></div>
        <div class="product"><div class="thumb"><div class="shot" role="img" aria-label="Red tax software box" style="background:linear-gradient(135deg,#c8141a,#e8b23a)"></div></div><div class="name">Software Name</div><div class="amount">$383.76</div><div class="actions"><a>Add to Cart</a><a class="details">Details</a></div></div>
        <div class="product"><div class="thumb"><div class="shot" role="img" aria-label="Blue painting software box" style="background:linear-gradient(135deg,#f3f3f3,#3a66b8)"></div></div><div class="name">Software Name</div><div class="amount">$151.29</div><div class="actions"><a>Add to Cart</a><a class="details">Details</a></div></div>

        <div class="product"><div class="thumb"><div class="shot" role="img" aria-label="Blue video software box" style="background:linear-gradient(135deg,#1f4f9a,#8fc0e8)"></div></div><div class="name">Software Name</div><div class="amount">$96</div><div class="actions"><a>Add to Cart</a><a class="details">Details</a></div></div>
        <div class="product"><div class="thumb"><div class="shot" role="img" aria-label="Red DVD player software box" style="background:linear-gradient(135deg,#c11a1a,#2a4f9a)"></div></div><div class="name">Software Name</div><div class="amount">$284</div><div class="actions"><a>Add to Cart</a><a class="details">Details</a></div></div>
        <div class="product"><div class="thumb"><div class="shot" role="img" aria-label="Red computer mouse" style="width:44px;height:24px;border-radius:12px;background:linear-gradient(135deg,#e23a2a,#8a0f0f)"></div></div><div class="name">Software Name</div><div class="amount">$383.76</div><div class="actions"><a>Add to Cart</a><a class="details">Details</a></div></div>
      </div>
    </main>
  </div>

  <footer class="footer">
    <div class="links">
      <a>Specials</a><a>Advanced Search</a><a>Reviews</a><a>Create an Account</a><a>Log In</a><a>Shipping &amp; Returns</a><a>Contact Us</a>
    </div>
    <div class="copy">Copyright © 2013 &nbsp;<a>Privacy Notice</a> &nbsp;| <a>Conditions of Use</a></div>
  </footer>
</body>
</html>
```